Two Versions of a Business Card for a Lawyer

Summary: I need a logo and a business card. The business card is two-sided and comes in two versions. One version is conservative, the other is slightly different with one or more pink embellishments in the logo or somewhere else in the business card.
I'm about to start off as a sole practitioner in criminal and immigration law. I'll largely be working with marginalised communities and in areas of social justice. One of my main focuses will be gendered violence, I'm hoping to specialise my practice towards representing victims of domestic and sexual violence and sex workers. I want a business card which would attract this clientele and make them feel safe to speak with me. I'd also like it to communicate a sense of hope.
However, the business card still has to be very conservative as the legal profession is very stuffy. So I was thinking of having two versions of the same card, one would be very straight forward while the other would have a **pink embellishment** or perhaps several. For example, if the scales of justice were used in the design, maybe the second version would have a pink flower about to bloom on the scale somewhere. Or maybe it's my logo that is different and pink.
While both designs have to be pretty conservative, I still want it to give off a sense that I'm alternative and think outside the box. With lawyers, I think a little bit of deviation goes a long way (less is more).
As far as colour goes (other than the pink embellishment), I was thinking something monochromatic, probably black and white but I am open to considering more colours. I personally love colour, and would love to use more colour, but am hesitant because of the nature of the profession. If you can find a way to use more colour while keeping it conservative and letting the pink pop, I'd be pretty pleased.
In general, I would prefer a clean simplistic design and logo. It should be immediately obvious that I'm a lawyer just by glancing at the card. I'm open to symbols of law, like the scales of justice or lady justice or something else. However, I don't want it to be the same as everyone else's.
Eventually, the design/style should be easy to recreate in the form of a website.
As far as the logo goes, it would probably use a circle as my last name starts with the letter "O". It can be very simple, with just my name and "Barrister & Solicitor". I don't currently have a logo, but the winning designer will be invited to provide a separate file for just the logo for an additional fee (I think it was CA$99). (Please ignore the uploaded logo file, it just wouldn't let me continue without uploading something).
As for the information that should go into the card, I'm still finalizing my address and phone number. So please use a placeholder for now.
Target Market(s)
Women, victims of sexual or domestic violence, refugees, people in need of legal services
Industry/Entity Type
Lawyer
Contact Information for Business Card
Marla Vent
Barrister & Solicitor
LL.B., B.C.L., B.F.A.
Criminal & Immigration Law
Street address
Toronto, ON
Postal Code
Phone number
Fax number
Email
Logo Text
Marla Vent, Barrister & Solicitor
Requirements
Must have
- Two versions
- One with pink
- Simplistic
Nice to have
- Maybe more colour
Should not have
- Not too conservative
- Not too predictable

```html
<!DOCTYPE html>
<html lang="en">
<head>
<meta charset="utf-8">
<title>Marla Vent — Business Cards</title>
<link href="https://fonts.googleapis.com/css2?family=Open+Sans:wght@300;400;600&display=swap" rel="stylesheet">
<style>
  :root {
    --canvas: #e9e7e4;
    --card: #0a0a0a;
    --ink: #ffffff;
    --band: #ffffff;
    --band-edge: #d8d8d8;
    --accent: #e8799f;
  }
  * { box-sizing: border-box; margin: 0; padding: 0; }
  html, body { width: 1200px; height: 891px; overflow: hidden; }
  body {
    background: var(--canvas);
    font-family: "Open Sans", Arial, sans-serif;
    color: var(--ink);
    position: relative;
  }
  .card {
    position: absolute;
    top: 140px;
    width: 340px;
    height: 600px;
    background: var(--card);
    box-shadow: 0 10px 28px rgba(0,0,0,0.25);
    overflow: hidden;
  }
  .card--front { left: 210px; }
  .card--back  { left: 650px; }
  .card__band {
    position: absolute;
    left: 0; right: 0; bottom: 0;
    height: 58px;
    background: var(--band);
    border-top: 6px solid var(--band-edge);
  }
  .card--pink .card__band { border-top-color: var(--accent); }
  .brand {
    position: absolute;
    display: flex;
    flex-direction: column;
    align-items: flex-start;
  }
  .brand__mark {
    width: 74px; height: 74px;
    border: 3px solid var(--ink);
    border-radius: 50%;
    margin-bottom: 18px;
  }
  .card--pink .brand__mark { border-color: var(--accent); }
  .brand__name {
    font-weight: 300;
    font-size: 38px;
    line-height: 1;
    padding: 8px 4px 6px;
    border-top: 2px solid var(--ink);
    border-bottom: 2px solid var(--ink);
    white-space: nowrap;
  }
  .card--front .brand { left: 70px; top: 190px; }
  .card--back .brand { left: 38px; top: 40px; }
  .card--back .brand__mark { width: 60px; height: 60px; margin-bottom: 14px; }
  .card--back .brand__name {
    font-size: 34px;
    border-top: none;
    padding: 0 2px 4px;
    border-bottom: 1.5px solid var(--ink);
  }
  .credentials {
    position: absolute;
    left: 40px; top: 168px;
    font-size: 14px;
    line-height: 1.4;
    padding-bottom: 6px;
    border-bottom: 1.5px solid var(--ink);
    width: 210px;
  }
  .credentials__degrees { word-spacing: 8px; }
  .contact {
    position: absolute;
    left: 40px; top: 248px;
    font-size: 14px;
    line-height: 1.55;
    width: 270px;
  }
  .contact__practice { font-weight: 300; font-size: 15px; margin-bottom: 16px; letter-spacing: 0.2px; }
  .contact__label { font-weight: 600; }
  .contact__row { display: flex; gap: 8px; }
  .contact__row .contact__label { min-width: 56px; }
</style>
</head>
<body>
  <section class="card card--front" aria-label="Card front, classic version">
    <div class="brand">
      <div class="brand__mark"></div>
      <div class="brand__name">Marla Vent</div>
    </div>
    <div class="card__band"></div>
  </section>

  <section class="card card--back card--pink" aria-label="Card back, pink accent version">
    <div class="brand">
      <div class="brand__mark"></div>
      <div class="brand__name">Marla Vent</div>
    </div>
    <div class="credentials">
      <div>Barrister &amp; Solicitor</div>
      <div class="credentials__degrees">LL.B. B.C.L. B.F.A.</div>
    </div>
    <div class="contact">
      <p class="contact__practice">Criminal &amp; Immigration Law</p>
      <p><span class="contact__label">Adresse:</span> Lorem ipsum dolor</p>
      <p>ifuim deom dulir Toronto, ON</p>
      <p>Postal Code:</p>
      <p><span class="contact__label">Email:</span> marla.vent@mailbox.com</p>
      <p class="contact__row"><span class="contact__label">Fax:</span> 00 00 00 00 00</p>
      <p class="contact__row"><span class="contact__label">Phone:</span> 00 00 00 00 00</p>
    </div>
    <div class="card__band"></div>
  </section>
</body>
</html>
```